Business card for medical clinic

I need an upmarket, modern medical/health business card for my clinic

Contact Information for Business Card

name, address, email, qr code

```html
<!DOCTYPE html>
<html lang="en">
<head>
<meta charset="utf-8">
<title>Meridia Care Clinic – Business Card</title>
<link href="https://fonts.googleapis.com/css2?family=Cinzel:wght@400;500&family=Arimo:wght@400&display=swap" rel="stylesheet">
<style>
  :root {
    --backdrop: #3a3a3c;
    --card-white: #ffffff;
    --brand-blue: #1c6aa8;
    --navy: #1a2a50;
    --navy-deep: #17233f;
    --cyan: #08a9e8;
    --ink-light: #ffffff;
  }
  * { box-sizing: border-box; margin: 0; padding: 0; }
  html, body { width: 1200px; height: 689px; overflow: hidden; }
  body {
    background: var(--backdrop);
    position: relative;
    font-family: "Arimo", Arial, sans-serif;
  }
  .card {
    position: absolute;
    top: 196px;
    width: 520px;
    height: 297px;
    border-radius: 16px;
    overflow: hidden;
  }
  .card-front { left: 50px; background: var(--card-white); }
  .card-back {
    left: 630px;
    background: radial-gradient(circle at 72% 46%, var(--cyan) 0%, #0a78bd 28%, var(--navy) 68%, var(--navy-deep) 100%);
    color: var(--ink-light);
  }

  /* wordmark */
  .wordmark {
    font-family: "Cinzel", "Times New Roman", serif;
    font-weight: 400;
    text-align: center;
    line-height: 1;
  }
  .wordmark-name { letter-spacing: 0.02em; }
  .wordmark-sub { letter-spacing: 0.42em; display: block; }
  .wordmark-rule { height: 1px; }

  .card-front .wordmark {
    position: absolute;
    left: 0; right: 0; top: 112px;
    color: var(--brand-blue);
  }
  .card-front .wordmark-name { font-size: 38px; }
  .card-front .wordmark-sub { font-size: 13px; margin-top: 8px; }
  .card-front .wordmark-rule {
    width: 300px; margin: 7px auto 0; background: var(--brand-blue);
  }

  .card-back .wordmark {
    position: absolute;
    left: 34px; top: 50px;
    color: var(--ink-light);
    text-align: left;
  }
  .card-back .wordmark-name { font-size: 22px; }
  .card-back .wordmark-sub { font-size: 8px; margin-top: 4px; text-align: center; }
  .card-back .wordmark-rule { width: 190px; margin-top: 4px; background: var(--ink-light); }

  .person { position: absolute; left: 34px; top: 120px; }
  .person-name {
    font-family: "Cinzel", "Times New Roman", serif;
    font-size: 22px; font-weight: 400; line-height: 1;
  }
  .person-role { font-size: 11px; margin-top: 4px; }

  .address { position: absolute; left: 34px; top: 170px; font-size: 11px; line-height: 1.3; font-style: normal; }

  .contact-list { position: absolute; left: 34px; top: 210px; list-style: none; font-size: 11px; }
  .contact-list li { display: flex; align-items: center; gap: 8px; height: 16px; }
  .contact-list svg { width: 10px; height: 10px; fill: var(--ink-light); flex: none; }
</style>
</head>
<body>

  <section class="card card-front" aria-label="Card front">
    <div class="wordmark">
      <span class="wordmark-name">MERIDIA CARE</span>
      <div class="wordmark-rule"></div>
      <span class="wordmark-sub">CLINIC</span>
    </div>
  </section>

  <section class="card card-back" aria-label="Card back">
    <div class="wordmark">
      <span class="wordmark-name">MERIDIA CARE</span>
      <div class="wordmark-rule"></div>
      <span class="wordmark-sub">CLINIC</span>
    </div>

    <div class="person">
      <p class="person-name">Daniel Harper</p>
      <p class="person-role">President</p>
    </div>

    <address class="address">
      4120 Willow Bend Road<br>
      Halden, Canada 28816
    </address>

    <ul class="contact-list">
      <li>
        <svg viewBox="0 0 10 10"><path d="M2 0.5 L3.6 2.6 L2.7 3.6 C3.3 5 4.9 6.7 6.4 7.3 L7.4 6.4 L9.5 8 L8.2 9.5 C4.5 9.2 0.8 5.5 0.5 1.8 Z"/></svg>
        <span>555-210-4837</span>
      </li>
      <li>
        <svg viewBox="0 0 10 10"><path d="M2.5 0 H7.5 V10 H2.5 Z M3.4 1 V8 H6.6 V1 Z"/></svg>
        <span>555-318-2960</span>
      </li>
      <li>
        <svg viewBox="0 0 10 10"><path d="M0 2 H10 V8.5 H0 Z M0.8 2.6 L5 5.8 L9.2 2.6 Z"/></svg>
        <span>info@meridiacare.com</span>
      </li>
      <li>
        <svg viewBox="0 0 10 10"><circle cx="5" cy="5" r="4.8"/></svg>
        <span>www.meridiacare.com</span>
      </li>
    </ul>
  </section>

</body>
</html>
```